Biz Card

MARKETING today is the most rapidly changing business discipline. Media options to reach customers, actual customer preferences and consumer buying decisions change by the minute . . . no, by the second. The behavioral data generated by all aspects of the business and the new technologies that put the data to work together produce the potential to generate business intelligence and guide smart resource allocation to influence purchase and retention. However, to realize this potential, marketing professionals at all levels and in all organizations must continuously improve their skills not just from on-the-job training but by learning from masters in the field. The Bright Horizon Guild is the training center that serves this professional development need.model logos:msi.orgama.orgcontentmarketinginstitute.comBook covers on MarketingMetrics, Marketing Anaytics
Industry/Entity Type
Business
Contact Information for Business Card
Roy A. YoungCEOMarketing Science Academyphone: 310-601-4755email: roy@marketingscience.comAddress:437 South Rexford DriveBeverly Hills, CA 89377
Look and feel
Each slider illustrates characteristics of the customer's brand and the style your logo design should communicate.

```html
<!DOCTYPE html>
<html lang="en">
<head>
<meta charset="utf-8">
<title>Bright Horizon Guild – Business Card</title>
<link rel="stylesheet" href="https://fonts.googleapis.com/css2?family=Roboto:wght@400;700;900&display=swap">
<style>
  :root {
    --backdrop: #a9a7a7;
    --brand-red: #8b2825;
    --card-white: #f7f7f6;
    --ink-gray: #4a4a4a;
    --text-gray: #5a5a5a;
    --white: #ffffff;
  }
  * { margin: 0; padding: 0; box-sizing: border-box; }
  html, body {
    width: 1200px; height: 1200px; overflow: hidden;
    background: var(--backdrop);
    font-family: "Roboto", Arial, sans-serif;
  }
  .canvas { position: relative; width: 1200px; height: 1200px; }

  .card { position: absolute; width: 713px; height: 418px; }
  .card-front { left: 238px; top: 118px; background: var(--brand-red); }
  .card-back { left: 230px; top: 644px; background: var(--card-white); }

  /* front wordmark */
  .front-mark {
    position: absolute; left: 0; right: 0; top: 160px;
    display: flex; align-items: center; justify-content: center; gap: 18px;
  }
  .front-mark .dot {
    width: 22px; height: 22px; border-radius: 50%; background: var(--white);
  }
  .front-mark .name {
    color: var(--white); font-weight: 900; font-size: 42px;
    letter-spacing: 1px; text-transform: uppercase; line-height: 1;
  }

  /* back wordmark */
  .back-mark {
    position: absolute; left: 78px; top: 118px; width: 266px;
  }
  .back-mark .dot {
    width: 24px; height: 24px; border-radius: 50%; background: var(--brand-red);
    margin-bottom: 14px;
  }
  .back-mark .name {
    color: var(--brand-red); font-weight: 900; font-size: 44px;
    line-height: 1.02; text-transform: uppercase; letter-spacing: 0.5px;
  }

  /* contact block */
  .contact { position: absolute; left: 410px; top: 100px; color: var(--text-gray); }
  .contact .person {
    color: var(--brand-red); font-weight: 700; font-size: 25px; line-height: 1;
  }
  .contact .role { font-size: 15px; margin-top: 12px; letter-spacing: 0.5px; }
  .contact .address { font-size: 17px; line-height: 24px; margin-top: 30px; }
  .contact .lines { list-style: none; margin-top: 9px; font-size: 17px; }
  .contact .lines li { display: flex; align-items: center; height: 24px; }
  .contact .lines svg { width: 16px; height: 16px; margin: 0 20px 0 2px; fill: var(--brand-red); }
</style>
</head>
<body>
<main class="canvas">
  <section class="card card-front" aria-label="Card front">
    <div class="front-mark">
      <span class="dot"></span>
      <span class="name">Bright Horizon Guild</span>
    </div>
  </section>

  <section class="card card-back" aria-label="Card back">
    <div class="back-mark">
      <div class="dot"></div>
      <div class="name">Bright<br>Horizon<br>Guild</div>
    </div>

    <div class="contact">
      <p class="person">Neil P. Barton</p>
      <p class="role">CEO</p>
      <p class="address">912 North Calloway Lane<br>Beverly Hills, CA 89377</p>
      <ul class="lines">
        <li>
          <svg viewBox="0 0 16 16" aria-hidden="true"><path d="M1 5c0-2 3-3 7-3s7 1 7 3v1h-4V5H5v1H1z"/><path d="M3 7h10l1 7H2z"/><circle cx="8" cy="10.5" r="2" fill="#f7f7f6"/></svg>
          310-555-0182
        </li>
        <li>
          <svg viewBox="0 0 16 16" aria-hidden="true"><path d="M1 3h14v10H1z"/><path d="M1 3l7 6 7-6" fill="none" stroke="#f7f7f6" stroke-width="1.4"/></svg>
          neil@brighthorizonguild.com
        </li>
        <li>
          <svg viewBox="0 0 16 16" aria-hidden="true"><circle cx="8" cy="8" r="7"/><path d="M1 8h14M8 1v14M3 4h10M3 12h10" stroke="#f7f7f6" stroke-width="1" fill="none"/><ellipse cx="8" cy="8" rx="3" ry="7" fill="none" stroke="#f7f7f6" stroke-width="1"/></svg>
          www.brighthorizonguild.com
        </li>
      </ul>
    </div>
  </section>
</main>
</body>
</html>
```